Letter and Envelope Design For Harborline Realty

Please design a letter and an envelope incorporating our logo (See Attached). We are also launched a business card contest. Since we want them to match, please feel free to submit a design for both the business card and also the letter design and envelope.

Requirements
Must have
• The envelope, the letter and the business cards must match somehow connecting the designs. We want them to have something that holds them together besides the logo.

```html
<!DOCTYPE html>
<html lang="en">
<head>
<meta charset="utf-8">
<title>Harborline Realty – Letterhead and Envelopes</title>
<link rel="stylesheet" href="https://fonts.googleapis.com/css2?family=Montserrat:wght@400;600&family=Roboto:wght@400&display=swap">
<style>
  :root {
    --backdrop: #dcdcdc;
    --paper: #f8f8f8;
    --brand-blue: #021a8c;
    --ink: #4a4a4a;
    --ink-soft: #5a5a5a;
    --ring: #e9eaee;
    --rule: #c9ccd8;
  }
  * { margin: 0; padding: 0; box-sizing: border-box; }
  html, body { width: 1200px; height: 877px; overflow: hidden; }
  body { background: var(--backdrop); position: relative; font-family: "Montserrat", sans-serif; color: var(--ink); }

  .sheet { position: absolute; background: var(--paper); overflow: hidden; box-shadow: 0 2px 10px rgba(0,0,0,.12); }
  .letter { left: 69px; top: 64px; width: 527px; height: 742px; }
  .envelope-back { left: 614px; top: 269px; width: 531px; height: 241px; }
  .envelope-front { left: 614px; top: 563px; width: 533px; height: 242px; }

  .ring { position: absolute; border-radius: 50%; border: 12px solid var(--ring); }
  .letter .ring { width: 312px; height: 312px; left: 235px; top: 512px; }
  .envelope-front .ring { width: 240px; height: 240px; left: 298px; top: 53px; border-width: 9px; }

  .brand { position: absolute; display: flex; flex-direction: column; align-items: center; color: var(--brand-blue); font-family: "Montserrat", sans-serif; font-weight: 600; }
  .brand-dot { border: 2px solid var(--brand-blue); border-radius: 50%; }
  .brand-name { letter-spacing: .14em; line-height: 1; }
  .brand-sub { display: flex; align-items: center; letter-spacing: .3em; line-height: 1; }
  .brand-sub::before, .brand-sub::after { content: ""; display: block; height: 1.5px; background: var(--brand-blue); }

  .letter .brand { left: 0; width: 100%; top: 42px; }
  .letter .brand-dot { width: 46px; height: 46px; margin-bottom: 10px; }
  .letter .brand-name { font-size: 13.5px; }
  .letter .brand-sub { font-size: 9px; margin-top: 4px; }
  .letter .brand-sub::before, .letter .brand-sub::after { width: 26px; }
  .letter .brand-sub::before { margin-right: 6px; }
  .letter .brand-sub::after { margin-left: 4px; }

  .salutation { position: absolute; left: 46px; top: 273px; font-size: 13.5px; color: var(--ink-soft); font-weight: 400; }
  .letter-body { position: absolute; left: 46px; top: 310px; width: 438px; font-size: 7.4px; line-height: 11.4px; color: var(--ink-soft); text-align: justify; }
  .letter-body p { margin-bottom: 11.4px; }
  .closing { position: absolute; left: 46px; top: 549px; font-size: 7.4px; color: var(--ink-soft); }
  .signature { position: absolute; left: 42px; top: 582px; width: 96px; height: 38px; background: linear-gradient(90deg, rgba(2,26,140,.08), rgba(2,26,140,.14)); border-radius: 3px; }

  .contact { position: absolute; left: 47px; top: 658px; font-family: "Roboto", sans-serif; font-size: 8px; line-height: 10.5px; color: var(--ink); }
  .contact li { list-style: none; display: flex; align-items: center; gap: 5px; }
  .contact svg { width: 7px; height: 7px; fill: var(--brand-blue); }
  .contact-divider { position: absolute; left: 221px; top: 672px; width: 1px; height: 26px; background: var(--rule); }
  .letter .address { position: absolute; left: 232px; top: 683px; }
  .address { font-family: "Roboto", sans-serif; font-size: 8px; line-height: 10px; color: var(--ink); }

  .flap { position: absolute; left: 0; top: 0; width: 531px; height: 74px; }
  .flap-brand { position: absolute; left: 0; width: 100%; top: 26px; display: flex; justify-content: center; align-items: center; gap: 7px; color: #fff; font-weight: 600; font-size: 10px; letter-spacing: .14em; }
  .flap-brand .brand-dot { width: 22px; height: 22px; border-color: #fff; }

  .envelope-front .brand { left: 26px; top: 21px; }
  .envelope-front .brand-dot { width: 38px; height: 38px; margin-bottom: 7px; }
  .envelope-front .brand-name { font-size: 11px; }
  .envelope-front .brand-sub { font-size: 7.5px; margin-top: 3px; }
  .envelope-front .brand-sub::before, .envelope-front .brand-sub::after { width: 24px; }
  .envelope-front .brand-sub::before { margin-right: 5px; }
  .envelope-front .brand-sub::after { margin-left: 3px; }
  .envelope-front .address { position: absolute; left: 28px; top: 98px; }
</style>
</head>
<body>

<section class="sheet letter">
  <div class="ring"></div>
  <div class="brand">
    <div class="brand-dot"></div>
    <div class="brand-name">HARBORLINE</div>
    <div class="brand-sub">REALTY</div>
  </div>

  <p class="salutation">Dear Mr. Reyes,</p>
  <div class="letter-body">
    <p>Lorem ipsum dolor sit amet, consectetur adipiscing elit. Donec orci purus, luctus vitae dignissim eu, iaculis sed purus. Vivamus faucibus, ipsum nec aliquet viverra, leo mauris condimentum ligula, sit amet sagittis enim ligula quis arcu. Nam egestas tortor id nisi porttitor mattis. In tortor ante, ultricies in suscipit a, tempus non massa. Vivamus et auctor mi. Fusce vel massa nulla. Phasellus nec eros mauris, et scelerisque orci.</p>
    <p>Donec malesuada orci vitae nulla accumsan porta a id massa. Quisque accumsan iaculis magna sit amet fringilla. Maecenas consequat, magna eget tincidunt semper, odio nibh rutrum mi, id feugiat ante nisi eu risus. Vestibulum nunc orci, rhoncus a placerat in, ultricies in mi. Cras mattis varius eros, vel fringilla nisi suscipit eget. Quisque scelerisque sagittis nulla at porttitor.</p>
    <p>Sed id augue vitae urna euismod commodo aliquet a quam. Pellentesque arcu velit, cursus et malesuada ut, consequat et diam. Nullam erat sem, rhoncus id ullamcorper vitae, rhoncus et arcu. In ultricies ultricies nulla, ut rutrum nisi iaculis at. Donec eu magna a metus ornare faucibus. Fusce aliquet faucibus ultricies. Morbi semper, est id tincidunt gravida, sem arcu adipiscing lacus, ac bibendum nulla leo eu purus. Quisque nec diam sed risus consectetur a accumsan quis quis nibh. Vestibulum id purus lorem.</p>
    <p>It is a long established fact that a reader will be distracted by the readable content of a page when looking at its layout. The point of using Lorem Ipsum is that it has a more-or-less normal distribution of letters, as opposed to using 'Content here, content here', making it look like readable English. Many desktop publishing packages</p>
  </div>
  <p class="closing">Sincerely,</p>
  <div class="signature" role="img" aria-label="Handwritten signature of Daniel Reyes in blue ink"></div>

  <ul class="contact">
    <li><svg viewBox="0 0 10 10"><path d="M2 0.5 L3.8 2.6 L2.9 3.8 Q4 6 6.2 7.1 L7.4 6.2 L9.5 8 L8.3 9.5 Q4.5 9.5 0.5 1.7 Z"/></svg>907 412 3380</li>
    <li><svg viewBox="0 0 10 10"><path d="M2.5 0 H7.5 V10 H2.5 Z M3.5 1.2 V7.8 H6.5 V1.2 Z"/></svg>907 655 2194</li>
    <li><svg viewBox="0 0 10 10"><path d="M0 2 H10 V8.5 H0 Z M0.8 2.6 L5 5.6 L9.2 2.6 Z"/></svg>hello@harborline.co</li>
    <li><svg viewBox="0 0 10 10"><circle cx="5" cy="5" r="4.8"/></svg>www.harborline.co</li>
  </ul>
  <div class="contact-divider"></div>
  <address class="address" style="font-style:normal">2140 Cedar Point Road<br>Juneau, Alaska 99801</address>
</section>

<section class="sheet envelope-back">
  <svg class="flap" viewBox="0 0 531 74" aria-hidden="true">
    <path d="M0 0 H531 L523 44 Q518 74 488 74 H43 Q12 74 8 44 Z" fill="var(--brand-blue)"/>
  </svg>
  <div class="flap-brand"><div class="brand-dot"></div>HARBORLINE REALTY</div>
</section>

<section class="sheet envelope-front">
  <div class="ring"></div>
  <div class="brand">
    <div class="brand-dot"></div>
    <div class="brand-name">HARBORLINE</div>
    <div class="brand-sub">REALTY</div>
  </div>
  <address class="address" style="font-style:normal">2140 Cedar Point Road<br>Juneau, Alaska 99801</address>
</section>

</body>
</html>
```